Clear Coat 5L & 2.5L kit

Clear coat 5 Liter with 2.5 Liter hardener
I attached few examples
Required size:
5L
Actual size is: 22.875 x 10.4375 inch
With bleed added: 23.125 x 10.6875 inch
2.5L
Actual size is: 22.875 x 6.1875 inch
With bleed added: 23.125x6.2125 inch

Thanks

```html
<!DOCTYPE html>
<html lang="en">
<head>
<meta charset="utf-8">
<title>Kestrel Refinish – Ultra Clear Coat Kit Labels</title>
<link href="https://fonts.googleapis.com/css2?family=Montserrat:wght@700;800&family=Roboto+Condensed:wght@300;400;700&display=swap" rel="stylesheet">
<style>
  :root{
    --page-top:#f3f6f8;
    --page-bottom:#cbdbe3;
    --label-navy:#0b1020;
    --label-deep:#0f1c36;
    --panel-black:#05070e;
    --brand-yellow:#f5c518;
    --accent-teal:#5ec8b4;
    --ink-white:#ffffff;
    --ink-soft:#d9dee6;
  }
  *{box-sizing:border-box;margin:0;padding:0}
  html,body{width:1200px;height:1038px;overflow:hidden}
  body{background:linear-gradient(180deg,var(--page-top),var(--page-bottom));font-family:"Roboto Condensed",Arial,sans-serif;color:var(--ink-white)}
  .canvas{position:relative;width:1200px;height:1038px;overflow:hidden}

  .label{position:absolute;background:linear-gradient(180deg,var(--label-navy) 0%,var(--label-deep) 60%,var(--label-navy) 100%);overflow:hidden}
  .label--clearcoat{left:63px;top:113px;width:1086px;height:497px}
  .label--hardener{left:64px;top:650px;width:1088px;height:293px}
  .label__wave{position:absolute;inset:0;width:100%;height:100%}

  .spine-title{position:absolute;writing-mode:vertical-rl;transform:rotate(180deg);font-size:17px;letter-spacing:.3px;font-weight:700;white-space:nowrap}
  .spine-title .light{color:var(--accent-teal);font-weight:300}
  .label--clearcoat .spine-title{left:22px;top:48px}
  .label--hardener .spine-title{left:20px;top:34px}

  .panel{position:absolute;background:var(--panel-black)}

  .brand{font-family:"Montserrat",Arial,sans-serif;font-weight:800;color:var(--ink-white);line-height:.95;display:flex;align-items:flex-start;gap:6px}
  .brand__dot{display:inline-block;border-radius:50%;background:var(--brand-yellow);flex:none}
  .brand__name{display:block}

  /* front panels */
  .front--clearcoat{left:209px;top:47px;width:238px;height:450px}
  .front--clearcoat .brand{position:absolute;left:30px;top:40px;font-size:34px}
  .front--clearcoat .brand__dot{width:15px;height:15px;margin-top:8px}
  .front--hardener{left:226px;top:28px;width:214px;height:265px}
  .front--hardener .brand{position:absolute;left:42px;top:20px;font-size:27px}
  .front--hardener .brand__dot{width:12px;height:12px;margin-top:6px}

  .product-line{position:absolute;color:var(--accent-teal);font-weight:300;font-size:20px;line-height:1}
  .product-name{position:absolute;font-family:"Montserrat",Arial,sans-serif;font-weight:700;line-height:1;white-space:nowrap}
  .voc{position:absolute;font-weight:700;font-size:13px;line-height:1}
  .front--clearcoat .product-line{left:34px;top:168px}
  .front--clearcoat .product-name{left:31px;top:188px;font-size:28px}
  .front--clearcoat .voc{left:34px;top:222px}
  .front--hardener .product-line{left:42px;top:114px;font-size:14px}
  .front--hardener .product-name{left:42px;top:130px;font-size:16px;letter-spacing:.5px;line-height:17px}
  .front--hardener .voc{left:42px;top:167px;font-size:9px}
  .speed-tag{position:absolute;right:22px;top:167px;color:var(--brand-yellow);font-weight:700;font-size:9px;letter-spacing:.8px;line-height:1}

  .features{position:absolute;left:124px;top:332px;list-style:none;font-weight:300;font-size:16px;line-height:28px;color:var(--ink-soft)}
  .features .mix{font-weight:700;color:var(--ink-white)}
  .volume{position:absolute;color:var(--brand-yellow);font-family:"Montserrat",Arial,sans-serif;font-weight:700;line-height:1}
  .front--clearcoat .volume{left:26px;top:392px;font-size:40px}
  .front--hardener .volume{left:34px;top:228px;font-size:20px}
  .front--hardener .mix-ratio{position:absolute;left:142px;top:232px;font-weight:700;font-size:12px;line-height:1}

  /* side panels */
  .side{font-size:5px;line-height:1.45;color:var(--ink-soft)}
  .side--clearcoat{left:528px;top:47px;width:122px;height:450px;padding:18px 10px 0 12px}
  .side--hardener{left:530px;top:28px;width:118px;height:265px;padding:10px 8px 0 8px;font-size:3.6px}
  .side .brand{font-size:16px;gap:4px;margin-bottom:32px}
  .side .brand__dot{width:7px;height:7px;margin-top:4px}
  .side h3{font-weight:700;color:var(--ink-white);font-size:inherit;margin-top:8px}
  .side p{margin:0}
  .side .caps{text-transform:uppercase}
  .maker{position:absolute;left:12px;top:360px;font-size:7px;line-height:1.5;color:var(--ink-white)}
  .side--hardener .maker{left:8px;top:190px;font-size:6px}
  .maker .origin{margin-top:10px;display:block;font-weight:700}
  .side--hardener .maker .origin{margin-top:8px}
  .litres{position:absolute;writing-mode:vertical-rl;transform:rotate(180deg);color:var(--brand-yellow);font-family:"Montserrat",Arial,sans-serif;font-weight:700;white-space:nowrap}
  .side--clearcoat .litres{right:8px;bottom:34px;font-size:17px}
  .side--hardener .litres{right:4px;bottom:20px;font-size:10px}

  /* back panels */
  .back{font-size:5.4px;line-height:1.4;color:var(--ink-soft)}
  .back--clearcoat{left:723px;top:47px;width:253px;height:450px;padding:20px 12px 0 10px}
  .back--hardener{left:732px;top:28px;width:229px;height:265px;padding:8px 8px 0 8px;font-size:3.7px}
  .back .brand{justify-content:flex-end;font-size:19px;gap:4px;margin-bottom:22px}
  .back .brand__dot{width:8px;height:8px;margin-top:4px}
  .back h3{font-weight:700;color:var(--ink-white);font-size:inherit;margin-top:6px;text-transform:uppercase}
  .back--hardener h3{margin-top:4px}
  .caution{position:absolute;left:10px;top:380px;width:140px;font-size:5.2px}
  .back--hardener .caution{left:8px;top:220px;width:130px;font-size:4.4px}
  .caution h3{font-size:7px;font-weight:400;color:var(--ink-white);margin:0 0 10px;letter-spacing:.2px}
  .back--hardener .caution h3{font-size:6.5px;margin-bottom:6px}
  .danger{position:absolute;border:1px solid var(--brand-yellow);display:flex;gap:5px;justify-content:center;align-items:flex-end}
  .back--clearcoat .danger{right:12px;top:382px;width:90px;height:46px;padding-bottom:6px}
  .back--hardener .danger{right:8px;top:222px;width:80px;height:40px;padding-bottom:5px}
  .danger__title{position:absolute;top:-6px;left:50%;transform:translateX(-50%);background:var(--panel-black);padding:0 4px;color:var(--brand-yellow);font-weight:700;font-size:10px;letter-spacing:1px;line-height:1}
  .back--hardener .danger__title{font-size:9px}
  .hazard{width:21px;height:21px}
  .back--hardener .hazard{width:19px;height:19px}
</style>
</head>
<body>
<div class="canvas">

  <section class="label label--clearcoat">
    <svg class="label__wave" viewBox="0 0 1086 497" preserveAspectRatio="none" role="img" aria-label="Flowing teal dotted wave pattern across the label background">
      <defs>
        <radialGradient id="waveGlowA" cx="0.25" cy="0.85" r="0.6">
          <stop offset="0" stop-color="#3f9e93" stop-opacity=".55"/>
          <stop offset="1" stop-color="#3f9e93" stop-opacity="0"/>
        </radialGradient>
        <radialGradient id="waveGlowB" cx="0.7" cy="0.2" r="0.4">
          <stop offset="0" stop-color="#3f9e93" stop-opacity=".35"/>
          <stop offset="1" stop-color="#3f9e93" stop-opacity="0"/>
        </radialGradient>
      </defs>
      <rect width="1086" height="497" fill="url(#waveGlowA)"/>
      <rect width="1086" height="497" fill="url(#waveGlowB)"/>
    </svg>

    <div class="spine-title"><span class="light">ULTRA</span> CLEAR COAT</div>

    <div class="panel front--clearcoat">
      <div class="brand"><span class="brand__name">KESTREL<br>REFINISH</span><span class="brand__dot"></span></div>
      <div class="product-line">ULTRA</div>
      <div class="product-name">CLEAR COAT</div>
      <div class="voc">VOC 2.1</div>
      <ul class="features">
        <li>High Gloss</li>
        <li>Good Leveling</li>
        <li>Easy Application</li>
        <li class="mix">2:1 MIX</li>
      </ul>
      <div class="volume">5L</div>
    </div>

    <div class="panel side side--clearcoat">
      <div class="brand"><span class="brand__name">KESTREL<br>REFINISH</span><span class="brand__dot"></span></div>
      <p class="caps">For use only by professionals<br>Not for sale or use by general public</p>
      <h3>NOTICE TO PURCHASER - Limited Warranty.</h3>
      <p>Seller guarantees this product meets its published specification when stored and applied as directed. Buyer assumes all risk of use and handling beyond these instructions. Liability is limited to replacement of product.</p>
      <h3>WARNING!</h3>
      <p class="caps">Contains flammable solvents. Keep away from heat, sparks and open flame. Use only with adequate ventilation and approved respirator. Keep container closed when not in use.</p>
      <h3>WARRANTY:</h3>
      <p>This product is warranted free of defects for twelve months from date of manufacture when stored sealed between 5 and 30 °C. Mix two parts clear coat with one part hardener by volume. Apply two medium wet coats with a short flash between coats. Results depend on surface preparation, film build and booth conditions beyond our control.</p>
      <div class="maker">Kestrel Refinish, Inc.<br>240 Harbor Ridge Rd,<br>Fenwick, CA 90210<br>(555) 014-2298<span class="origin">Made in EU</span></div>
      <div class="litres">5 LITERS</div>
    </div>

    <div class="panel back back--clearcoat">
      <div class="brand"><span class="brand__name">KESTREL<br>REFINISH</span><span class="brand__dot"></span></div>
      <h3>Description:</h3>
      <p>A premium two component urethane clear coat for automotive refinishing. Delivers high gloss, excellent flow and leveling, and fast through cure. Suitable for spot, panel and overall repairs over basecoat systems. Resists UV, chemicals and fuel once fully cured. Sands and polishes easily for a show finish.</p>
      <h3>Warning! Flammable. Vapor and spray mist harmful. May cause lung irritation and allergic respiration reaction</h3>
      <p>Contains isocyanates and organic solvents. Vapors may cause dizziness, drowsiness and irritation of eyes, skin and respiratory tract. Repeated exposure may cause sensitization. Do not breathe spray mist. Wear a supplied air or approved respirator, protective gloves, goggles and coveralls during mixing, application and cleanup. Keep away from heat, sparks and open flame. Ground containers when transferring. Vapors are heavier than air and may travel to a source of ignition. Store in a cool, dry, well ventilated area away from oxidizers. Dispose of waste according to local regulations. Do not pour into drains or waterways. Empty containers may retain hazardous residue.</p>
      <h3>First aid:</h3>
      <p>If inhaled, move to fresh air and keep at rest. In case of eye contact, rinse with water for fifteen minutes and seek medical attention. On skin, wash thoroughly with soap and water and remove contaminated clothing. If swallowed, do not induce vomiting; call a poison center or doctor immediately.</p>
      <h3>Notice:</h3>
      <p>Information on this label is based on tests believed reliable. Always read the technical data sheet and safety data sheet before use.</p>
      <div class="caution">
        <h3>KEEP OUT OF THE REACH OF CHILDREN</h3>
        <p>Harmful if inhaled or swallowed. Keep container tightly closed. Avoid contact with eyes and skin. Read safety data sheet before use.</p>
      </div>
      <div class="danger">
        <span class="danger__title">DANGER</span>
        <svg class="hazard" viewBox="0 0 24 24" aria-label="Flammable"><circle cx="12" cy="12" r="11" fill="#fff" stroke="#c0272d" stroke-width="2"/><path d="M12 5c1 3 4 4 4 8a4 4 0 0 1-8 0c0-2 1-3 2-4 0 2 1 2 1 2 0-3 1-4 1-6z" fill="#111"/></svg>
        <svg class="hazard" viewBox="0 0 24 24" aria-label="Health hazard"><circle cx="12" cy="12" r="11" fill="#fff" stroke="#c0272d" stroke-width="2"/><rect x="10.5" y="5" width="3" height="9" fill="#111"/><rect x="10.5" y="16" width="3" height="3" fill="#111"/></svg>
        <svg class="hazard" viewBox="0 0 24 24" aria-label="Toxic"><circle cx="12" cy="12" r="11" fill="#fff" stroke="#c0272d" stroke-width="2"/><path d="M7 7l10 10M17 7L7 17" stroke="#111" stroke-width="3"/></svg>
      </div>
    </div>
  </section>

  <section class="label label--hardener">
    <svg class="label__wave" viewBox="0 0 1088 293" preserveAspectRatio="none" role="img" aria-label="Flowing teal dotted wave pattern across the label background">
      <defs>
        <radialGradient id="waveGlowC" cx="0.2" cy="0.6" r="0.55">
          <stop offset="0" stop-color="#3f9e93" stop-opacity=".5"/>
          <stop offset="1" stop-color="#3f9e93" stop-opacity="0"/>
        </radialGradient>
        <radialGradient id="waveGlowD" cx="0.72" cy="0.15" r="0.35">
          <stop offset="0" stop-color="#3f9e93" stop-opacity=".35"/>
          <stop offset="1" stop-color="#3f9e93" stop-opacity="0"/>
        </radialGradient>
      </defs>
      <rect width="1088" height="293" fill="url(#waveGlowC)"/>
      <rect width="1088" height="293" fill="url(#waveGlowD)"/>
    </svg>

    <div class="spine-title"><span class="light">ULTRA</span> HARDENER</div>

    <div class="panel front--hardener">
      <div class="brand"><span class="brand__name">KESTREL<br>REFINISH</span><span class="brand__dot"></span></div>
      <div class="product-line">ULTRA</div>
      <div class="product-name">HARDENER<br>FOR CEAR COAT</div>
      <div class="voc">VOC 2.1</div>
      <div class="speed-tag">SLOW</div>
      <div class="volume">2.5L</div>
      <div class="mix-ratio">2:1 MIX</div>
    </div>

    <div class="panel side side--hardener">
      <p class="caps">For use only by professionals<br>Not for sale or use by general public</p>
      <h3>NOTICE TO PURCHASER - Limited Warranty.</h3>
      <p>Seller guarantees this product meets its published specification when stored and applied as directed. Buyer assumes all risk of use and handling beyond these instructions. Liability is limited to replacement of product.</p>
      <h3>WARNING!</h3>
      <p class="caps">Contains isocyanates and flammable solvents. Keep away from heat, sparks and open flame. Use only with adequate ventilation and approved respirator. Keep container closed when not in use.</p>
      <h3>WARRANTY:</h3>
      <p>This product is warranted free of defects for twelve months from date of manufacture when stored sealed between 5 and 30 °C. Add one part hardener to two parts clear coat by volume. Protect from moisture; reseal immediately after use. Results depend on surface preparation, film build and booth conditions beyond our control.</p>
      <div class="maker">Kestrel Refinish, Inc.<br><br>240 Harbor Ridge Rd,<br>Fenwick, CA 90210<br>(555) 014-2298<span class="origin">Made in EU</span></div>
      <div class="litres">2.5 LITERS</div>
    </div>

    <div class="panel back back--hardener">
      <h3>Description:</h3>
      <p>A slow isocyanate hardener matched to the ultra clear coat for warm booth conditions. Extends open time for improved flow and leveling on large panels and overall refinishes. Mix one part hardener to two parts clear coat by volume and stir thoroughly before spraying.</p>
      <h3>Warning! Flammable. Vapor and spray mist harmful. May cause lung irritation and allergic respiration reaction</h3>
      <p>Contains isocyanates and organic solvents. Vapors may cause dizziness, drowsiness and irritation of eyes, skin and respiratory tract. Repeated exposure may cause sensitization. Do not breathe spray mist. Wear a supplied air or approved respirator, protective gloves, goggles and coveralls during mixing, application and cleanup. Keep away from heat, sparks and open flame. Ground containers when transferring. Vapors are heavier than air and may travel to a source of ignition. Store in a cool, dry, well ventilated area away from oxidizers. Dispose of waste according to local regulations. Do not pour into drains or waterways. Empty containers may retain hazardous residue.</p>
      <h3>First aid:</h3>
      <p>If inhaled, move to fresh air and keep at rest. In case of eye contact, rinse with water for fifteen minutes and seek medical attention. On skin, wash thoroughly with soap and water and remove contaminated clothing. If swallowed, do not induce vomiting; call a poison center or doctor immediately.</p>
      <h3>Notice:</h3>
      <p>Information on this label is based on tests believed reliable. Always read the technical data sheet and safety data sheet before use.</p>
      <div class="caution">
        <h3>KEEP OUT OF THE REACH OF CHILDREN</h3>
        <p>Harmful if inhaled or swallowed. Keep container tightly closed. Avoid contact with eyes and skin. Read safety data sheet before use.</p>
      </div>
      <div class="danger">
        <span class="danger__title">DANGER</span>
        <svg class="hazard" viewBox="0 0 24 24" aria-label="Flammable"><circle cx="12" cy="12" r="11" fill="#fff" stroke="#c0272d" stroke-width="2"/><path d="M12 5c1 3 4 4 4 8a4 4 0 0 1-8 0c0-2 1-3 2-4 0 2 1 2 1 2 0-3 1-4 1-6z" fill="#111"/></svg>
        <svg class="hazard" viewBox="0 0 24 24" aria-label="Health hazard"><circle cx="12" cy="12" r="11" fill="#fff" stroke="#c0272d" stroke-width="2"/><rect x="10.5" y="5" width="3" height="9" fill="#111"/><rect x="10.5" y="16" width="3" height="3" fill="#111"/></svg>
        <svg class="hazard" viewBox="0 0 24 24" aria-label="Toxic"><circle cx="12" cy="12" r="11" fill="#fff" stroke="#c0272d" stroke-width="2"/><path d="M7 7l10 10M17 7L7 17" stroke="#111" stroke-width="3"/></svg>
      </div>
    </div>
  </section>

</div>
</body>
</html>
```